Unique Business Card Design

Unique Business Card design for our orthotic and prosthetic company. Our logo is on our website, color is light blue. Unique shape (artificial leg shaped, vertical, etc..) preferred. Logo, business name, individual name and basic demographics needed.

Industry/Entity Type

Business

Contact Information for Business Card

Logo, Industry, Phone # Logo, "Prosthetic & Orthotic Services" Place to add individual name and contact info

Colors
cee9f5

Requirements
Must have
• The icon must be there, placement of "Prosthetic & Orthotic Services" can be moved
Nice to have
• Like the mix of light blue, and a little darker blue. One design included the icons from my website which was a nice touch

```html
<!DOCTYPE html>
<html lang="en">
<head>
<meta charset="utf-8">
<title>Limbworks Inc. – Business Card</title>
<link rel="stylesheet" href="https://fonts.googleapis.com/css2?family=Open+Sans:wght@400;700&family=Dancing+Script:wght@500&display=swap">
<style>
  :root {
    --brand-blue: #1f5fae;
    --brand-blue-dark: #174c8f;
    --light-blue: #cee9f5;
    --paper: #ffffff;
    --ink: #4a4a4a;
    --curve-shadow: #8a8a8a;
    --stage: #e8ebee;
  }
  html, body {
    margin: 0;
    width: 1200px;
    height: 950px;
    overflow: hidden;
    background: var(--stage);
    font-family: "Open Sans", Arial, sans-serif;
  }
  .sheet { position: relative; width: 1200px; height: 950px; }
  .card {
    position: absolute;
    overflow: hidden;
    box-shadow: 0 6px 18px rgba(0,0,0,0.18);
  }
  .card--front { left: 30px; top: 125px; width: 700px; height: 400px; background: var(--paper); }
  .card--back  { left: 770px; top: 125px; width: 400px; height: 700px; background: var(--brand-blue); }

  .front-art { position: absolute; inset: 0; }

  .brand {
    position: absolute;
    left: 40px;
    top: 42px;
    display: flex;
    align-items: center;
    gap: 16px;
  }
  .brand__mark { width: 74px; height: 74px; border-radius: 50%; background: var(--brand-blue); flex: none; }
  .brand__name {
    margin: 0;
    font-size: 30px;
    font-weight: 700;
    color: var(--brand-blue);
    letter-spacing: 0.5px;
    line-height: 1;
    border-bottom: 2px solid var(--brand-blue);
    padding-bottom: 6px;
  }
  .brand__tagline {
    margin: 6px 0 0;
    font-family: "Dancing Script", cursive;
    font-size: 19px;
    color: var(--brand-blue);
  }

  .contact {
    position: absolute;
    left: 44px;
    top: 158px;
    color: var(--ink);
    font-size: 16px;
    line-height: 1.45;
  }
  .contact__address { margin: 0 0 8px; }
  .contact__list { list-style: none; margin: 0; padding: 0; }
  .contact__item { display: flex; align-items: center; gap: 10px; height: 27px; }
  .contact__icon { width: 18px; height: 18px; flex: none; }

  .person {
    position: absolute;
    right: 30px;
    top: 40px;
    text-align: right;
    color: var(--paper);
  }
  .person__name { margin: 0; font-size: 28px; font-weight: 400; line-height: 1.1; }
  .person__name b { font-weight: 700; }
  .person__title { margin: 6px 0 0; font-size: 16px; letter-spacing: 1px; }

  .back-emblem {
    position: absolute;
    left: 50%;
    top: 50%;
    width: 240px;
    height: 240px;
    margin: -120px 0 0 -120px;
    border-radius: 50%;
    background: var(--paper);
    display: flex;
    align-items: center;
    justify-content: center;
  }
  .back-emblem__name { font-size: 22px; font-weight: 700; color: var(--brand-blue); letter-spacing: 0.5px; }
  .back-web {
    position: absolute;
    left: 34px;
    top: 0;
    height: 700px;
    display: flex;
    align-items: center;
    writing-mode: vertical-rl;
    color: var(--paper);
    font-size: 15px;
    letter-spacing: 5px;
    white-space: nowrap;
  }
</style>
</head>
<body>
<main class="sheet">

  <section class="card card--front">
    <svg class="front-art" width="700" height="400" viewBox="0 0 700 400" aria-hidden="true">
      <path d="M372 0 Q612 150 548 400" fill="none" stroke="var(--curve-shadow)" stroke-width="14"/>
      <path d="M390 0 Q622 150 560 400 H700 V0 Z" fill="var(--brand-blue)"/>
    </svg>

    <header class="brand">
      <div class="brand__mark"></div>
      <div>
        <h1 class="brand__name">LIMBWORKS INC.</h1>
        <p class="brand__tagline">Prosthetic &amp; Orthotic Services</p>
      </div>
    </header>

    <div class="person">
      <h2 class="person__name"><b>Mira</b> Kessler</h2>
      <p class="person__title">CO LPO</p>
    </div>

    <div class="contact">
      <p class="contact__address">2250 Harbor Ave<br>Eastport, NY 11900</p>
      <ul class="contact__list">
        <li class="contact__item">
          <svg class="contact__icon" viewBox="0 0 18 18" aria-label="Phone"><circle cx="9" cy="9" r="9" fill="var(--brand-blue)"/><path d="M6 5 L8 5 L8.5 7 L7.5 8 Q8.5 10 10 10.5 L11 9.5 L13 10 L13 12 Q9 13 6 9 Q5 7 6 5Z" fill="#fff"/></svg>
          555.014.2200
        </li>
        <li class="contact__item">
          <svg class="contact__icon" viewBox="0 0 18 18" aria-label="Fax"><circle cx="9" cy="9" r="9" fill="var(--brand-blue)"/><rect x="6" y="4.5" width="6" height="3" fill="#fff"/><rect x="4.5" y="8" width="9" height="4" rx="1" fill="#fff"/><rect x="6" y="11" width="6" height="2.5" fill="#fff"/></svg>
          555.014.2291
        </li>
        <li class="contact__item">
          <svg class="contact__icon" viewBox="0 0 18 18" aria-label="Mobile"><circle cx="9" cy="9" r="9" fill="var(--brand-blue)"/><rect x="6.5" y="4" width="5" height="10" rx="1" fill="#fff"/><rect x="7.3" y="5.2" width="3.4" height="6.5" fill="var(--brand-blue)"/></svg>
          555-019.4470
        </li>
        <li class="contact__item">
          <svg class="contact__icon" viewBox="0 0 18 18" aria-label="Email"><circle cx="9" cy="9" r="9" fill="var(--brand-blue)"/><rect x="4.5" y="6" width="9" height="6.5" fill="#fff"/><path d="M4.5 6 L9 9.5 L13.5 6" fill="none" stroke="var(--brand-blue)" stroke-width="1"/></svg>
          mkessler@limbworksinc.com
        </li>
        <li class="contact__item">
          <svg class="contact__icon" viewBox="0 0 18 18" aria-label="Website"><circle cx="9" cy="9" r="9" fill="var(--brand-blue)"/><circle cx="9" cy="9" r="4.5" fill="none" stroke="#fff" stroke-width="1.2"/><path d="M4.5 9 H13.5 M9 4.5 Q6.5 9 9 13.5 M9 4.5 Q11.5 9 9 13.5" fill="none" stroke="#fff" stroke-width="1"/></svg>
          www.limbworksinc.com
        </li>
      </ul>
    </div>
  </section>

  <section class="card card--back">
    <p class="back-web">www.limbworksinc.com</p>
    <div class="back-emblem">
      <span class="back-emblem__name">LIMBWORKS INC.</span>
    </div>
  </section>

</main>
</body>
</html>
```